Velmoria-Quillmesh Partial Redesign - Web App

Are you able to apply your creativity to an existing layout? I’m convinced that even just a few touches can make a big difference to add personality and professionalism to a website design, and I’m looking for someone able to use existing ideas and bring them to the next level while keeping inside some given constraints.
The actual job is to improve an existing design concept and to apply it creatively to a landing page, a simple home page, and an older web app (single page website).
To help you start with a clear picture of the current situation and of my requirements, I created a detailed brief with screenshots, live examples, and complete instructions. You can find it attached to this job.
My tastes are inclined towards clean and simple designs. For this project I'm not looking for dazzling novelty, but for very solid craftsmanship. Are the right man - or woman - for the job?
Updates
I wanted to thank everybody who participated in this project. I made a choice, but also other designs were interesting. Hope to work with you another time.
Target Market(s)
Our main target is social media marketers and startuppers
Look and feel
Each slider illustrates characteristics of the customer's brand and the style your logo design should communicate.

```html
<!DOCTYPE html>
<html lang="en">
<head>
<meta charset="utf-8">
<title>Velmoria – Hashtag Explorer</title>
<link rel="stylesheet" href="https://fonts.googleapis.com/css2?family=Ubuntu:ital,wght@0,400;0,500;0,700;1,400;1,500&display=swap">
<style>
:root{
  --ink:#3c4047;
  --text:#4a4d52;
  --muted:#6b6e73;
  --blue:#3a98e8;
  --blue-dark:#1f86e0;
  --line:#2f8fe6;
  --side:#ececec;
  --white:#ffffff;
  --chirp:#36b7f0;
  --circle:#3c5a99;
  --ring:#3a3d42;
  --orange-a:#ffcd8e;
  --orange-b:#ffbc6c;
  --bar-orange:#eeaa3c;
  --bar-yellow:#eccb3a;
  --bar-grey:#cbc9cf;
}
*{margin:0;padding:0;box-sizing:border-box}
html,body{width:1200px;height:1078px;overflow:hidden;background:var(--white)}
body{font-family:"Ubuntu",sans-serif;color:var(--text)}
.page{position:relative;width:1280px;height:1150px;transform:scale(.9375);transform-origin:0 0}
.abs{position:absolute}

/* header */
.brand{left:160px;top:60px;display:flex;align-items:center;gap:16px}
.brand-dot{width:58px;height:58px;border-radius:50%;background:var(--ink)}
.brand-name{font-weight:700;font-size:38px;color:var(--ink);letter-spacing:-.5px}
.navbar{left:0;top:157px;width:1280px;height:36px;background:var(--ink)}
.nav{left:160px;top:157px;display:flex;height:36px}
.nav a{display:block;color:#fff;text-decoration:none;font-size:14px;line-height:36px;padding:0 17px;width:137px}
.nav a.active{background:var(--blue)}
.nav a + a{width:auto;padding:0 35px 0 52px}

/* sidebar */
.sidebar{left:795px;top:0;width:325px;height:1105px;background:var(--side);box-shadow:-6px 0 10px rgba(0,0,0,.08)}
.social{left:828px;width:265px;height:33px;display:flex;border:1px solid #d6d6d6;background:#fff}
.social .label{width:172px;height:31px;color:#fff;font-size:11px;line-height:31px;padding-left:44px}
.social .count{flex:1;font-size:14px;color:#222;line-height:31px;padding-left:20px}
.s-chirp .label{background:var(--chirp)}
.s-circle .label{background:var(--circle)}
.s-ring .label{background:var(--ring)}
.search{left:810px;top:197px;width:295px;height:36px;background:#e4e4e4;border-top:2px solid #cfcfcf;font-size:15px;color:#555;line-height:34px;padding-left:12px}
.search svg{position:absolute;right:12px;top:10px}
.stats{left:795px;top:268px;width:325px;height:158px;background:linear-gradient(var(--orange-a),var(--orange-b))}
.stats h3{position:absolute;left:15px;top:20px;font-weight:400;font-size:14px;color:#4a3a25}
.digits{position:absolute;left:15px;top:57px;display:flex;gap:5px}
.digits span{width:25px;height:35px;background:#fff;font-size:22px;line-height:35px;text-align:center;color:#666}
.stats p{position:absolute;left:15px;top:118px;font-size:14px;color:#4a3a25}
.feeds-head{left:810px;top:445px;display:flex;align-items:center;gap:22px;font-size:14px;color:#333}
.bird{width:45px;height:34px;border-radius:50%;background:linear-gradient(#9bdcf6,#3fb2e6)}
.feed{left:810px;width:295px;height:72px}
.avatar{position:absolute;left:2px;top:1px;width:44px;height:44px;border:2px solid #fff;box-shadow:0 1px 3px rgba(0,0,0,.25);background:linear-gradient(#b9a89a,#6a5a50)}
.feed .who{position:absolute;left:0;top:50px;font-size:12px;color:#333}
.bubble{position:absolute;left:63px;top:0;width:232px;height:72px;background:#fff;border:1px solid #d6d6d6;padding:5px 10px;font-size:10.5px;line-height:20px;color:#666;white-space:nowrap;overflow:hidden}
.bubble::before{content:"";position:absolute;left:-7px;top:12px;border:6px solid transparent;border-right-color:#fff;border-left:0}
.bubble em{color:var(--blue-dark)}

/* content */
.tabs{left:160px;top:268px;width:612px;height:34px;background:var(--blue);border-radius:3px;display:flex;align-items:flex-end;padding-left:8px}
.tabs span{font-style:italic;font-size:11px;color:#fff;height:26px;line-height:24px;padding:0 14px}
.tabs span.active{background:#fff;color:var(--blue-dark);border-radius:2px 2px 0 0}
.graph{left:190px;top:340px}
.graph text{font-family:"Ubuntu",sans-serif;font-size:12px;fill:#fff;text-anchor:middle}
.modes{left:615px;top:793px;display:flex;font-size:12px}
.modes span{height:27px;line-height:27px;padding:0 10px}
.modes .off{background:#a9d2f4;color:#2f7ec6}
.modes .on{background:var(--blue);color:#fff;padding:0 4px}
.section-title{left:160px;top:825px;font-style:italic;font-size:17px;color:var(--blue-dark);font-weight:400}
.ranking{left:160px;top:859px;list-style:none;font-size:14px;color:#333}
.ranking li{height:20px;line-height:20px}
.ranking b{display:inline-block;width:30px;font-weight:400}
.chart{left:330px;top:862px}
.chart text{font-family:"Ubuntu",sans-serif;font-size:12px;fill:#333}
.chart .barlabel{fill:#fff;font-size:12px}

/* footer */
.footer{left:0;top:1105px;width:1280px;height:45px;background:var(--ink);color:#c9ccd0;font-size:12px;line-height:45px}
.footer .copy{position:absolute;left:160px}
.footer .links{position:absolute;left:909px}
</style>
</head>
<body>
<div class="page">

  <div class="abs brand"><div class="brand-dot"></div><div class="brand-name">Velmoria</div></div>

  <div class="abs navbar"></div>
  <nav class="abs nav"><a class="active">Hash Tag</a><a>Blog</a><a>About</a></nav>

  <aside class="abs sidebar"></aside>
  <div class="abs social s-chirp" style="top:22px"><span class="label">Follow on Chirpline</span><span class="count">12,566</span></div>
  <div class="abs social s-circle" style="top:74px"><span class="label">Follow on Circlestream</span><span class="count">12,566</span></div>
  <div class="abs social s-ring" style="top:125px"><span class="label">Follow on Plusring</span><span class="count">12,566</span></div>

  <div class="abs search">Search
    <svg width="16" height="16" viewBox="0 0 16 16"><circle cx="6.5" cy="6.5" r="5" fill="none" stroke="#2f8fe6" stroke-width="2"/><line x1="10" y1="10" x2="14.5" y2="14.5" stroke="#2f8fe6" stroke-width="2.5"/></svg>
  </div>

  <section class="abs stats">
    <h3>Hashtags found so far :</h3>
    <div class="digits"><span>1</span><span>0</span><span>,</span><span>6</span><span>1</span><span>1</span><span>,</span><span>1</span><span>8</span><span>0</span></div>
    <p>in 567,419,411 tweets</p>
  </section>

  <div class="abs feeds-head"><div class="bird" role="img" aria-label="Small blue bird illustration"></div><span>Latest Chirpline Feeds :</span></div>

  <div class="abs feed" style="top:496px"><div class="avatar" role="img" aria-label="User profile photo"></div><span class="who">Dave</span><div class="bubble">At Orva communication, we believe results<br>are what matter most. With over 15 years<br><em>9 minutes ago</em></div></div>
  <div class="abs feed" style="top:582px"><div class="avatar" role="img" aria-label="User profile photo"></div><span class="who">Dave</span><div class="bubble">At Orva communication, we believe results<br>are what matter most. With over 15 years<br><em>9 minutes ago</em></div></div>
  <div class="abs feed" style="top:668px"><div class="avatar" role="img" aria-label="User profile photo"></div><span class="who">Dave</span><div class="bubble">At Orva communication, we believe results<br>are what matter most. With over 15 years<br><em>9 minutes ago</em></div></div>
  <div class="abs feed" style="top:753px"><div class="avatar" role="img" aria-label="User profile photo"></div><span class="who">Dave</span><div class="bubble">At Orva communication, we believe results<br>are what matter most. With over 15 years<br><em>9 minutes ago</em></div></div>
  <div class="abs feed" style="top:839px"><div class="avatar" role="img" aria-label="User profile photo"></div><span class="who">Dave</span><div class="bubble">At Orva communication, we believe results<br>are what matter most. With over 15 years<br><em>9 minutes ago</em></div></div>
  <div class="abs feed" style="top:925px"><div class="avatar" role="img" aria-label="User profile photo"></div><span class="who">Dave</span><div class="bubble">At Orva communication, we believe results<br>are what matter most. With over 15 years<br><em>9 minutes ago</em></div></div>
  <div class="abs feed" style="top:1009px"><div class="avatar" role="img" aria-label="User profile photo"></div><span class="who">Dave</span><div class="bubble">At Orva communication, we believe results<br>are what matter most. With over 15 years<br><em>9 minutes ago</em></div></div>

  <div class="abs tabs"><span class="active">Top Related Hashtags</span><span>Free Top Influencers</span><span>Free Variants</span><span>Free In-Depth Intelligence</span><span>Pro</span></div>

  <svg class="abs graph" width="540" height="470" viewBox="190 340 540 470">
    <defs><linearGradient id="bubbleFill" x1="0" y1="0" x2="0" y2="1"><stop offset="0" stop-color="#40a0ee"/><stop offset="1" stop-color="#1d86e2"/></linearGradient></defs>
    <g stroke="var(--line)" stroke-width="1">
      <line x1="455" y1="540" x2="438" y2="388"/><line x1="455" y1="540" x2="319" y2="425"/>
      <line x1="455" y1="540" x2="578" y2="406"/><line x1="455" y1="540" x2="648" y2="499"/>
      <line x1="455" y1="540" x2="244" y2="538"/><line x1="455" y1="540" x2="667" y2="625"/>
      <line x1="455" y1="540" x2="254" y2="669"/><line x1="455" y1="540" x2="383" y2="651"/>
      <line x1="455" y1="540" x2="557" y2="683"/><line x1="455" y1="540" x2="428" y2="752"/>
    </g>
    <g fill="url(#bubbleFill)">
      <circle cx="438" cy="388" r="37"/><circle cx="319" cy="425" r="44"/><circle cx="578" cy="406" r="43"/>
      <circle cx="648" cy="499" r="43"/><circle cx="244" cy="538" r="42"/><circle cx="667" cy="625" r="46"/>
      <circle cx="254" cy="669" r="50"/><circle cx="383" cy="651" r="43"/><circle cx="557" cy="683" r="42"/>
      <circle cx="428" cy="752" r="44"/><circle cx="455" cy="540" r="50"/>
    </g>
    <text x="438" y="392">500 day</text><text x="321" y="430">follow me</text><text x="578" y="410">100 day</text>
    <text x="650" y="504">jim</text><text x="240" y="537">Back</text><text x="670" y="630">instan follow</text>
    <text x="256" y="675">follow back</text><text x="387" y="655">follow</text><text x="556" y="687">instant follow</text>
    <text x="432" y="755">back</text><text x="455" y="542">auto follow</text>
  </svg>

  <div class="abs modes"><span class="off">Advace Mode</span><span class="on">Simple Mode</span></div>

  <h2 class="abs section-title">Hashtag Top Influencers</h2>
  <ol class="abs ranking">
    <li><b>1</b>bizgadgetry</li><li><b>2</b>lanavreet</li><li><b>3</b>corwinhale</li><li><b>4</b>mirelou_</li>
    <li><b>5</b>postlattice</li><li><b>6</b>tiptopthreads</li><li><b>7</b>qwkrqw</li><li><b>8</b>promo_swirl</li>
    <li><b>9</b>gearshift9</li><li><b>10</b>brightcoppermedia</li>
  </ol>

  <svg class="abs chart" width="345" height="215" viewBox="330 862 345 215">
    <line x1="360" y1="866" x2="360" y2="1048" stroke="var(--line)"/>
    <line x1="360" y1="1048" x2="669" y2="1048" stroke="var(--line)"/>
    <text transform="translate(347 1042) rotate(-90)" font-size="11">User Influence for this campaign</text>
    <polygon points="370,878 541,878 541,909 370,909 370,898 365,893 370,888" fill="var(--blue)"/>
    <text class="barlabel" x="388" y="897">Support 128312 followers</text>
    <polygon points="370,915 541,915 541,946 370,946 370,935 365,930 370,925" fill="var(--bar-orange)"/>
    <polygon points="370,952 541,952 541,983 370,983 370,972 365,967 370,962" fill="var(--bar-yellow)"/>
    <polygon points="370,989 541,989 541,1020 370,1020 370,1009 365,1004 370,999" fill="var(--bar-grey)"/>
    <text x="404" y="1068">User Specialization for this campaign</text>
  </svg>

  <footer class="abs footer">
    <span class="copy">Copyright (c) 2011-2012 Velmoria Ltd</span>
    <span class="links">Terms &amp; Condition &nbsp; | &nbsp; Privacy Policy</span>
  </footer>

</div>
</body>
</html>
```